Merrow Trade finance web design

We are a newly established business which provides invoice finance to Small Businesses in England and Wales.
Our approach is very much a funder where the small business owner can talk to the decision maker. We will guarantee on receipt of information, a decision within 24 hours.
We are not a bank so the look of the website need to be friendly but professional.
Have two types of people we are trying to attract to the website: 1) partners who are small business owners and 2) introducers who is accountants and commercial brokers who introduce us to the small businesses.
Currently no website, although domain has been reserved.
The design should be:
Professional
“Clean” Look
Designed to convey Trust and Authority.
Appeal to the small business owner.
Must incorporate:
Logo (attached)
Front page:Top tabs to other pages 1) About us 2) Services 3) Introducers 4) Contact us
Need picture and logo on page.
1) About us page- Room for talk about the company, the people and our critera.
2) Services page- We need for what invoice finance is, and 5 boxes for different services we will provide. (link on page to contact us)
3) Introducers page- We need a part for why become an introducer? Who we can help? Why we are different? (link on page to contact us)
4) Contact us page- Office address, email, tel and if possible a map and a contact me part which will email direct to us.
Text will be provided for the design, if we can see the setup of the website we will provide a part for each of the pages to support.
Styles we think convey the correct image:
www.dornelcapital.example
www.plivanlend.example
www.quorbacredit.example
Target Market(s)
Small business owners
Industry/Entity Type
Finance
Number of Pages Required
5+ page
Look and feel

```html
<!DOCTYPE html>
<html lang="en">
<head>
<meta charset="utf-8">
<title>Merrow Trade Finance</title>
<link rel="stylesheet" href="https://fonts.googleapis.com/css2?family=Roboto:wght@300;400;500;700&family=Playball&display=swap">
<style>
:root{
  --red:#e5323a;
  --red-dark:#c9262d;
  --ink:#222222;
  --text:#666666;
  --light:#eeeeee;
  --footer:#222222;
  --white:#ffffff;
  --photo-a:#5d6f86;
}
*{box-sizing:border-box;margin:0;padding:0}
html,body{width:1200px;height:3158px;overflow:hidden}
body{font-family:"Roboto",Arial,sans-serif;color:var(--text);background:var(--white)}
.accent{color:var(--red)}
.btn{display:inline-block;background:var(--red);color:var(--white);font-size:21px;font-weight:400;border-radius:30px;padding:0 26px;height:56px;line-height:56px;text-transform:uppercase;box-shadow:0 4px 8px rgba(0,0,0,.15);text-decoration:none;white-space:nowrap}

/* hero */
.hero{position:relative;height:678px;background:linear-gradient(135deg,#b9c6d4 0%,var(--photo-a) 45%,#2f3946 75%,#6f7f90 100%)}
.hero-photo{position:absolute;inset:0}
.topbar{position:absolute;top:0;left:0;right:0;height:120px;background:rgba(255,255,255,.88);display:flex;align-items:center;padding:0 40px 0 78px}
.brand{display:flex;align-items:center;gap:12px;font-size:30px;font-weight:700;color:var(--red);white-space:nowrap}
.brand-dot{width:22px;height:22px;border-radius:50%;background:var(--red);flex:none}
.nav{margin-left:auto;display:flex;gap:10px;align-items:center}
.nav a{font-size:17px;color:var(--ink);text-decoration:none;padding:0 14px;height:46px;line-height:46px;border-radius:24px;white-space:nowrap}
.nav a.active{background:var(--red);color:var(--white);padding:0 26px}
.hero-title{position:absolute;left:0;right:0;top:540px;text-align:center;font-family:"Playball",cursive;font-size:52px;color:var(--white);text-shadow:0 2px 6px rgba(0,0,0,.5)}
.slide-arrow{position:absolute;top:364px;width:50px;height:50px;border:2px solid rgba(255,255,255,.7);border-radius:50%}
.slide-arrow.prev{left:10px}.slide-arrow.next{right:10px}
.slide-arrow svg{width:100%;height:100%}

/* services */
.services{display:flex;height:332px}
.service{flex:1;text-align:center;box-shadow:6px 0 14px -6px rgba(0,0,0,.18)}
.service-head{height:187px;background:var(--red);color:var(--white);padding-top:40px}
.service.featured .service-head{background:var(--red-dark)}
.service-head svg{width:80px;height:70px}
.service-head h3{font-size:19px;font-weight:400;margin-top:22px;white-space:nowrap}
.service p{font-size:14px;line-height:24px;padding:26px 24px 0}
.chev{display:block;width:16px;height:14px;margin:8px auto 0}

/* welcome */
.welcome{height:390px;text-align:center;padding-top:46px}
.section-title{font-size:44px;font-weight:400;color:var(--ink)}
.welcome p{font-size:14px;line-height:27px;width:900px;margin:12px auto 20px}

/* about */
.about{position:relative;height:522px;background:linear-gradient(90deg,#f2f2f2 0%,#e8e6e3 40%,#b7a48e 65%,#7d6b5a 100%)}
.about-copy{position:absolute;left:78px;top:62px;width:680px}
.about h2{font-size:42px;font-weight:400;color:var(--ink)}
.about h4{font-size:19px;font-weight:400;color:var(--ink);margin:14px 0 10px}
.about p{font-size:14px;line-height:27px;color:#555;margin-bottom:14px}

/* introducers */
.introducers{height:440px;text-align:center;padding-top:56px}
.intro-cols{display:flex;width:1050px;margin:30px auto 0;text-align:left}
.intro-col{flex:1;padding:0 0 0 2px}
.intro-col+.intro-col{border-left:1px solid #e4e4e4;padding-left:20px}
.intro-col h4{font-size:18px;font-weight:400;color:var(--ink);margin-bottom:16px}
.intro-col p{font-size:14px;line-height:27px;margin-bottom:12px;padding-right:14px}

/* contact */
.contact{height:469px;background:var(--light);text-align:center;padding-top:52px}
.contact>p{font-size:14px;line-height:27px;width:900px;margin:12px auto 24px}
.form{width:892px;margin:0 auto;text-align:left}
.row{display:flex;gap:8px}
.field{flex:1;height:52px;border:1px solid #ccc;background:#f5f5f5;font-size:15px;color:#555;padding:15px 12px}
.field.msg{height:104px;margin-top:10px}
.contact .btn{margin-top:10px}

/* footer */
.footer{height:268px;background:var(--footer);display:flex;padding:28px 78px 0;gap:30px}
.fcol{width:236px}
.fcol h5{font-size:17px;font-weight:400;color:var(--red);margin-bottom:20px}
.links{list-style:none}
.links li{font-size:14px;color:#ddd;line-height:27px}
.links li::before{content:"›";margin-right:10px;font-size:18px}
.ginfo{display:flex;gap:16px;font-size:14px;color:#ddd;line-height:22px;margin-bottom:12px}
.ginfo svg{width:18px;height:18px;flex:none;margin-top:2px}
.ginfo b{font-weight:500;color:#fff}
.map{width:248px;height:164px;background:linear-gradient(135deg,#e9e4d6,#d8dcc8 50%,#c9d3de)}
.news p{font-size:14px;color:#ddd;line-height:22px}
.email{margin-top:12px;height:42px;background:#fff;font-size:14px;color:#555;padding:12px 12px}
.footer .btn{margin-top:12px;height:46px;line-height:46px;font-size:18px;padding:0 30px}
.copy{height:59px;background:var(--red);color:#fff;text-align:center;font-size:14px;line-height:59px}
</style>
</head>
<body>

<header class="hero">
  <div class="hero-photo" role="img" aria-label="Photo of a business team gathered around a table in a bright modern office"></div>
  <div class="topbar">
    <div class="brand"><span class="brand-dot"></span>Merrow Trade Finance</div>
    <nav class="nav">
      <a class="active" href="#">HOME</a>
      <a href="#">ABOUT US</a>
      <a href="#">SERVICES</a>
      <a href="#">INTRODUCERS</a>
      <a href="#">CONTACT US</a>
    </nav>
  </div>
  <span class="slide-arrow prev"><svg viewBox="0 0 50 50"><path d="M29 16 20 25l9 9" fill="none" stroke="#fff" stroke-width="2"/></svg></span>
  <span class="slide-arrow next"><svg viewBox="0 0 50 50"><path d="M21 16l9 9-9 9" fill="none" stroke="#fff" stroke-width="2"/></svg></span>
  <div class="hero-title">Trade Finance Limited</div>
</header>

<section class="services">
  <div class="service">
    <div class="service-head">
      <svg viewBox="0 0 80 70" fill="#fff"><rect x="6" y="46" width="10" height="20"/><rect x="22" y="36" width="10" height="30"/><rect x="38" y="28" width="10" height="38"/><rect x="54" y="18" width="10" height="48"/><path d="M4 38 28 18l12 8 24-20" fill="none" stroke="#fff" stroke-width="5"/><path d="M56 2h14v14z"/></svg>
      <h3>SERVICES ONE</h3>
    </div>
    <p>Lorem Ipsum is simply text of dummy text of the printing and type setting..</p>
    <svg class="chev" viewBox="0 0 16 14"><path d="M2 1l6 5 6-5M2 7l6 5 6-5" fill="none" stroke="var(--red)" stroke-width="2"/></svg>
  </div>
  <div class="service">
    <div class="service-head">
      <svg viewBox="0 0 80 70"><rect x="16" y="4" width="40" height="54" rx="3" fill="#fff"/><circle cx="30" cy="20" r="8" fill="var(--red)"/><rect x="42" y="16" width="10" height="3" fill="var(--red)"/><rect x="22" y="34" width="28" height="3" fill="var(--red)"/><rect x="22" y="42" width="22" height="3" fill="var(--red)"/><circle cx="56" cy="54" r="12" fill="#fff" stroke="var(--red)" stroke-width="3"/><path d="M50 54l4 4 8-8" fill="none" stroke="var(--red)" stroke-width="3"/></svg>
      <h3>SERVICES TWO</h3>
    </div>
    <p>Lorem Ipsum is simply text of dummy text of the printing and type setting..</p>
    <svg class="chev" viewBox="0 0 16 14"><path d="M2 1l6 5 6-5M2 7l6 5 6-5" fill="none" stroke="var(--red)" stroke-width="2"/></svg>
  </div>
  <div class="service featured">
    <div class="service-head">
      <svg viewBox="0 0 80 70" fill="#fff"><ellipse cx="32" cy="12" rx="24" ry="8"/><path d="M8 18c0 5 11 9 24 9s24-4 24-9v10c0 5-11 9-24 9S8 33 8 28z"/><path d="M8 34c0 5 11 9 24 9s24-4 24-9v10c0 5-11 9-24 9S8 49 8 44z"/><circle cx="56" cy="46" r="11" fill="none" stroke="#fff" stroke-width="5"/><path d="M63 54l12 12" stroke="#fff" stroke-width="6"/></svg>
      <h3>SERVICES THREE</h3>
    </div>
    <p>Lorem Ipsum is simply text of dummy text of the printing and type setting..</p>
    <svg class="chev" viewBox="0 0 16 14"><path d="M2 1l6 5 6-5M2 7l6 5 6-5" fill="none" stroke="var(--red)" stroke-width="2"/></svg>
  </div>
  <div class="service">
    <div class="service-head">
      <svg viewBox="0 0 80 70" fill="none" stroke="#fff" stroke-width="3"><path d="M30 50c0-8-8-12-8-22a18 18 0 0 1 36 0c0 10-8 14-8 22z"/><path d="M32 56h16M34 62h12"/><path d="M40 2v4M14 10l4 4M66 10l-4 4M6 30h5M69 30h5"/></svg>
      <h3>SERVICES FOUR</h3>
    </div>
    <p>Lorem Ipsum is simply text of dummy text of the printing and type setting..</p>
    <svg class="chev" viewBox="0 0 16 14"><path d="M2 1l6 5 6-5M2 7l6 5 6-5" fill="none" stroke="var(--red)" stroke-width="2"/></svg>
  </div>
  <div class="service">
    <div class="service-head">
      <svg viewBox="0 0 80 70"><rect x="6" y="6" width="58" height="42" rx="2" fill="none" stroke="#fff" stroke-width="4"/><path d="M28 48v10h16V48M20 60h32" stroke="#fff" stroke-width="4" fill="none"/><rect x="16" y="26" width="5" height="14" fill="#fff"/><rect x="25" y="20" width="5" height="20" fill="#fff"/><rect x="34" y="16" width="5" height="24" fill="#fff"/><circle cx="58" cy="44" r="10" fill="var(--red)" stroke="#fff" stroke-width="4"/><path d="M65 51l9 9" stroke="#fff" stroke-width="5"/></svg>
      <h3>SERVICES FIVE</h3>
    </div>
    <p>Lorem Ipsum is simply text of dummy text of the printing and type setting..</p>
    <svg class="chev" viewBox="0 0 16 14"><path d="M2 1l6 5 6-5M2 7l6 5 6-5" fill="none" stroke="var(--red)" stroke-width="2"/></svg>
  </div>
</section>

<section class="welcome">
  <h2 class="section-title">WELCOME TO <span class="accent">MERROW</span></h2>
  <p>Lorem Ipsum is simply dummy text of the printing and typesetting industry. Lorem Ipsum has been the industry's standard dummy text ever since the 1500s, when an unknown printer took a galley of type and scrambled it to make a type specimen book.<br>It has survived not only five centuries. Lorem Ipsum is simply dummy text of the printing and typesetting industry. Lorem Ipsum has been the industry's standard dummy text ever since the 1500s, when an unknown printer took a galley of type and scrambled it to make a type specimen book. It has survived not only five centuries.</p>
  <a class="btn" href="#">KNOW MORE</a>
</section>

<section class="about" role="img" aria-label="Photo of two businessmen reviewing documents at a desk, fading to white on the left">
  <div class="about-copy">
    <h2>ABOUT <span class="accent">MERROW</span></h2>
    <h4>Trade Finance Limited</h4>
    <p>Lorem Ipsum is simply dummy text of the printing and typesetting industry. Lorem Ipsum has been the industry's standard dummy text ever since the 1500s, when an unknown printer took a galley of type and scrambled it to make a type specimen book. Lorem Ipsum is simply dummy text of the printing and typesetting industry Lorem Ipsum has been the.</p>
    <p>It has survived not only five centuries. Lorem Ipsum is simply dummy text of the printing and typesetting industry. Lorem Ipsum has been the industry's standard dummy text ever since the 1500s, when an unknown printer took a galley of type and scrambled it to make a type specimen book. It has survived not only five centuries.</p>
    <a class="btn" href="#">KNOW MORE</a>
  </div>
</section>

<section class="introducers">
  <h2 class="section-title">OUR <span class="accent">INTRODUCERS</span></h2>
  <div class="intro-cols">
    <div class="intro-col">
      <h4>WHY BECOME AN INTRODUCER ?</h4>
      <p>Lorem Ipsum is simply dummy text of the printing and typesetting industry. Lorem Ipsum has been the industry's standard dummy text ever since the when an unknown printer took a galley of type and scrambled it to make a specimen book.</p>
      <a class="btn" href="#">CONTACT US</a>
    </div>
    <div class="intro-col">
      <h4>WHO WE HELP ?</h4>
      <p>Lorem Ipsum is simply dummy text of the printing and typesetting industry. Lorem Ipsum has been the industry's standard dummy text ever since the when an unknown printer took a galley of type and scrambled it to make a specimen book.</p>
      <a class="btn" href="#">CONTACT US</a>
    </div>
    <div class="intro-col">
      <h4>WHY WE ARE DIFFERENT ?</h4>
      <p>Lorem Ipsum is simply dummy text of the printing and typesetting industry. Lorem Ipsum has been the industry's standard dummy text ever since the when an unknown printer took a galley of type and scrambled it to make a specimen book.</p>
      <a class="btn" href="#">CONTACT US</a>
    </div>
  </div>
</section>

<section class="contact">
  <h2 class="section-title">CONTACT <span class="accent">US</span></h2>
  <p>Lorem Ipsum is simply dummy text of the printing and typesetting industry. Lorem Ipsum has been the industry's standard dummy text ever since the 1500s, when an unknown printer took.</p>
  <div class="form">
    <div class="row"><div class="field">Name*</div><div class="field">Email*</div><div class="field">Phone*</div></div>
    <div class="field msg">Message*</div>
  </div>
  <a class="btn" href="#">SUBMIT</a>
</section>

<footer class="footer">
  <div class="fcol">
    <h5>USEFULL LINKS</h5>
    <ul class="links"><li>Home</li><li>About Us</li><li>Services</li><li>Introducer</li><li>Contact Us</li></ul>
  </div>
  <div class="fcol">
    <h5>GET IN TOUCH</h5>
    <div class="ginfo"><svg viewBox="0 0 18 18"><path d="M9 1a6 6 0 0 0-6 6c0 5 6 10 6 10s6-5 6-10a6 6 0 0 0-6-6z" fill="none" stroke="var(--red)" stroke-width="1.5"/><circle cx="9" cy="7" r="2" fill="var(--red)"/></svg><div><b>MERROW</b><br>Lorem ipsum dolor amet simple. Dummy text of printting &amp; type setting industry.</div></div>
    <div class="ginfo"><svg viewBox="0 0 18 18"><path d="M4 1l3 4-2 2c1 3 3 5 6 6l2-2 4 3-2 3C8 17 1 10 1 3z" fill="none" stroke="var(--red)" stroke-width="1.5"/></svg><div>123 456 789</div></div>
    <div class="ginfo"><svg viewBox="0 0 18 18"><rect x="1" y="4" width="16" height="11" fill="none" stroke="var(--red)" stroke-width="1.5"/><path d="M1 4l8 6 8-6" fill="none" stroke="var(--red)" stroke-width="1.5"/></svg><div>info@merrowtrade.example</div></div>
  </div>
  <div class="fcol">
    <h5>NEWSLETTER</h5>
    <div class="map" role="img" aria-label="Street map showing the office location"></div>
  </div>
  <div class="fcol news">
    <h5>NEWSLETTER</h5>
    <p>Would you like to receive exclusive access to articles, white papers and our regular monthly newsletter?</p>
    <div class="email">Email Id</div>
    <a class="btn" href="#">SUBSCRIBE</a>
  </div>
</footer>
<div class="copy">©MERROW - 2016 All rights reserved.</div>

</body>
</html>
```